Northfield Builders Guild Business card

We are looking for a new business card design with photo included.
Our business is a nonprofit construction contractor membership organization. We offer business education, assist with business setup and licensing, provide safety training, and provide a member directory.
URL: www.builderslinkguild.org
Color code:
CMYK: 0 cyan, 42 magenta, 100 yellow, 0 black for Print.
Hexidecimal: #FF9900
RGB: R 255; G 153; B 0

```html
<!DOCTYPE html>
<html lang="en">
<head>
<meta charset="utf-8">
<title>Northfield Builders Guild – Business Card</title>
<link href="https://fonts.googleapis.com/css2?family=Arimo:wght@400;700&display=swap" rel="stylesheet">
<style>
  :root{
    --orange:#f7971e;
    --charcoal:#333233;
    --ink:#2f2e30;
    --white:#ffffff;
    --backdrop:#2a2a2a;
  }
  *{box-sizing:border-box;margin:0;padding:0}
  html,body{width:1200px;height:1015px;overflow:hidden}
  body{
    background:var(--backdrop);
    font-family:"Arimo",Arial,sans-serif;
    position:relative;
  }
  .card{
    position:absolute;
    left:250px;
    width:700px;height:400px;
    overflow:hidden;
    box-shadow:0 10px 30px rgba(0,0,0,.5);
  }
  /* Front */
  .card-front{top:60px;background:var(--orange)}
  .front-name{
    position:absolute;left:0;right:0;top:120px;
    text-align:center;
    color:var(--ink);
    font-weight:700;
    font-size:50px;
    line-height:1.05;
    letter-spacing:.5px;
    text-transform:uppercase;
  }
  .front-url{
    position:absolute;left:0;right:0;top:308px;
    text-align:center;
    color:var(--ink);
    font-size:17px;
    letter-spacing:1.5px;
  }
  /* Back */
  .card-back{top:535px;background:var(--charcoal)}
  .card-back .shape{position:absolute;inset:0}
  .back-name{
    position:absolute;left:400px;width:280px;top:140px;
    text-align:center;
    color:var(--ink);
    font-weight:700;
    font-size:29px;
    line-height:1.1;
    text-transform:uppercase;
  }
  .person{position:absolute;left:40px;top:62px}
  .person-name{color:var(--orange);font-weight:700;font-size:26px;letter-spacing:.3px}
  .person-role{color:var(--white);font-size:15px;letter-spacing:.5px;margin-top:2px}
  .contacts{position:absolute;left:40px;top:138px;list-style:none}
  .contacts li{
    display:flex;align-items:center;gap:10px;
    color:var(--white);font-size:18px;height:27px;
  }
  .contacts .note{color:var(--orange)}
  .icon{
    width:22px;height:22px;border-radius:50%;
    background:var(--orange);
    display:flex;align-items:center;justify-content:center;flex:none;
  }
  .address{
    position:absolute;left:72px;top:262px;
    color:var(--white);font-size:18px;line-height:1.3;
  }
  .back-url{
    position:absolute;left:72px;top:354px;
    color:var(--orange);font-size:18px;letter-spacing:.3px;
  }
</style>
</head>
<body>

<section class="card card-front">
  <p class="front-name">Northfield<br>Builders Guild</p>
  <p class="front-url">www.builderslinkguild.org</p>
</section>

<section class="card card-back">
  <svg class="shape" width="700" height="400" viewBox="0 0 700 400">
    <circle cx="560" cy="150" r="250" fill="var(--white)"/>
    <path d="M335 60 A250 250 0 0 0 520 398" fill="none" stroke="var(--orange)" stroke-width="5"/>
  </svg>

  <p class="back-name">Northfield<br>Builders Guild</p>

  <div class="person">
    <p class="person-name">DANIEL HARPER</p>
    <p class="person-role">MANAGING DIRECTOR</p>
  </div>

  <ul class="contacts">
    <li>
      <span class="icon"><svg width="12" height="12" viewBox="0 0 24 24"><path d="M6 2l4 4-2 3c1 3 4 6 7 7l3-2 4 4-3 4C10 22 2 14 2 5z" fill="var(--white)"/></svg></span>
      (555) 010-4292 <span class="note">(Office)</span>
    </li>
    <li>
      <span class="icon"><svg width="10" height="13" viewBox="0 0 10 14"><rect x="1" y="1" width="8" height="12" rx="1.5" fill="none" stroke="var(--white)" stroke-width="1.6"/></svg></span>
      555-010-4125
    </li>
    <li>
      <span class="icon"><svg width="13" height="12" viewBox="0 0 14 13"><rect x="3.5" y="0.5" width="7" height="4" fill="var(--white)"/><rect x="0.5" y="4.5" width="13" height="5" rx="1" fill="var(--white)"/><rect x="3.5" y="8" width="7" height="4.5" fill="var(--white)" stroke="var(--orange)"/></svg></span>
      555.010.0880
    </li>
    <li>
      <span class="icon"><svg width="13" height="10" viewBox="0 0 14 10"><rect x="0.5" y="0.5" width="13" height="9" fill="var(--white)"/><path d="M0.5 0.5 L7 6 L13.5 0.5" fill="none" stroke="var(--orange)" stroke-width="1.2"/></svg></span>
      support@nbguild.org
    </li>
  </ul>

  <p class="address">2400 Elm Ridge Rd<br>Suite #100, Northfield<br>OR 97000</p>
  <p class="back-url">www.builderslinkguild.org</p>
</section>

</body>
</html>
```